Pinecroft Ridge A4 Potrait foldout brochure

We need a brochure design for this residential land development. I have attached the a style that we like to base our design on. Full colour required. will provide files required for design also. PLEASE DO NOT COPY THIS DESIGN. Come up with a new style that gives you this feeling. Please note the plan needs to be positioned landscape on the inside 2 A4 Pages.

Industry/Entity Type

Residential

Font styles to use
Other font styles liked:
• Try with Century Gothich

Requirements
Must have
• use same colours as supplied in Pinecroft ridge brochure.
Nice to have
• nice modern simple background graphics

```html
<!DOCTYPE html>
<html lang="en">
<head>
<meta charset="utf-8">
<title>Pinecroft Ridge – Masterplan Brochure Covers</title>
<link rel="stylesheet" href="https://fonts.googleapis.com/css2?family=Questrial&family=Kalam:wght@300&display=swap">
<style>
  :root {
    --forest: #08491f;
    --leaf: #62bb46;
    --lime: #8dc63f;
    --violet: #93379a;
    --plum: #7c4ba0;
    --sun: #ffc20e;
    --tangerine: #f7941d;
    --paper: #ffffff;
    --stage: #ece8e1;
  }
  html, body {
    margin: 0;
    padding: 0;
    width: 1200px;
    height: 839px;
    overflow: hidden;
    background: var(--stage);
  }
  .spread {
    position: relative;
    width: 1200px;
    height: 839px;
  }
  .page {
    position: absolute;
    top: 35px;
    width: 544px;
    height: 768px;
    display: block;
    box-shadow: 0 2px 8px rgba(0,0,0,0.25);
  }
  .page--back { left: 42px; }
  .page--front { left: 610px; }
  .brand-name {
    font-family: "Questrial", "Century Gothic", sans-serif;
  }
  .contact {
    font-family: "Questrial", "Century Gothic", sans-serif;
    font-size: 12px;
    fill: var(--paper);
  }
  .contact--phone { font-size: 15px; font-weight: bold; }
  .title {
    font-family: "Kalam", cursive;
    font-weight: 300;
  }
</style>
</head>
<body>
<main class="spread">

  <!-- Back cover -->
  <svg class="page page--back" viewBox="0 0 680 960" xmlns="http://www.w3.org/2000/svg">
    <defs>
      <linearGradient id="corner-sun" x1="0" y1="0" x2="1" y2="0">
        <stop offset="0" stop-color="var(--sun)"/>
        <stop offset="1" stop-color="var(--tangerine)"/>
      </linearGradient>
      <linearGradient id="corner-leaf" x1="0" y1="0" x2="1" y2="0">
        <stop offset="0" stop-color="var(--lime)"/>
        <stop offset="1" stop-color="var(--leaf)"/>
      </linearGradient>
    </defs>
    <rect class="page-ground" width="680" height="960" fill="var(--forest)"/>
    <polygon class="corner corner--top-left" points="0,0 160,0 0,160" fill="var(--leaf)"/>
    <polygon class="corner corner--top-right" points="520,0 680,0 680,160" fill="var(--violet)"/>
    <polygon class="corner corner--bottom-left" points="0,800 0,960 160,960" fill="url(#corner-sun)"/>
    <polygon class="corner corner--bottom-right" points="680,800 680,960 520,960" fill="url(#corner-leaf)"/>

    <g class="brand-diamond">
      <polygon points="340,320 500,480 340,640 180,480" fill="var(--paper)"/>
      <circle cx="340" cy="450" r="14" fill="var(--leaf)"/>
      <text class="brand-name" x="340" y="510" text-anchor="middle" font-size="26" fill="var(--forest)">Pinecroft Ridge</text>
      <text class="brand-name" x="443" y="520" text-anchor="end" font-size="7" fill="var(--forest)">Harrow Vale</text>
    </g>

    <g class="contact-row">
      <path d="M117,651 a5,5 0 1 1 10,0 c0,4 -5,9 -5,9 c0,0 -5,-5 -5,-9 z" fill="var(--paper)"/>
      <circle cx="122" cy="651" r="1.8" fill="var(--forest)"/>
      <text class="contact" x="129" y="660">12345 Abcdef Ghijklmn,</text>
      <text class="contact" x="125" y="679">Opqrst uvwxyz 00000</text>

      <circle cx="281" cy="675" r="5.5" fill="none" stroke="var(--paper)" stroke-width="1.4"/>
      <text class="contact contact--phone" x="289" y="681">000-000-0000</text>

      <rect x="414" y="653" width="11" height="8" fill="none" stroke="var(--paper)" stroke-width="1.3"/>
      <path d="M414,653 l5.5,4.5 l5.5,-4.5" fill="none" stroke="var(--paper)" stroke-width="1.3"/>
      <text class="contact" x="428" y="661">info@PinecroftRidge.com</text>

      <circle cx="420" cy="676" r="4.5" fill="none" stroke="var(--paper)" stroke-width="1.3"/>
      <line x1="415.5" y1="676" x2="424.5" y2="676" stroke="var(--paper)" stroke-width="1"/>
      <text class="contact" x="428" y="680">www.PinecroftRidge.com</text>
    </g>
  </svg>

  <!-- Front cover -->
  <svg class="page page--front" viewBox="0 0 680 960" xmlns="http://www.w3.org/2000/svg">
    <defs>
      <linearGradient id="mosaic-tones" x1="0" y1="0" x2="1" y2="1">
        <stop offset="0" stop-color="var(--plum)"/>
        <stop offset="0.3" stop-color="var(--leaf)"/>
        <stop offset="0.55" stop-color="var(--sun)"/>
        <stop offset="0.75" stop-color="var(--violet)"/>
        <stop offset="1" stop-color="var(--tangerine)"/>
      </linearGradient>
    </defs>
    <rect class="page-ground" width="680" height="960" fill="var(--forest)"/>
    <path class="mosaic-field" role="img" aria-label="Stained-glass style mosaic of purple, green, yellow and orange panels"
          d="M0,0 H680 V596 C520,590 300,610 200,690 C120,750 110,830 165,880 C90,850 30,800 0,700 Z"
          fill="url(#mosaic-tones)"/>
    <text class="title" x="417" y="462" text-anchor="middle" font-size="50" fill="var(--paper)">Masterplan</text>

    <g class="brand-lockup">
      <circle cx="340" cy="810" r="14" fill="var(--leaf)"/>
      <text class="brand-name" x="340" y="888" text-anchor="middle" font-size="32" fill="var(--paper)">Pinecroft Ridge</text>
      <text class="brand-name" x="469" y="898" text-anchor="end" font-size="8" fill="var(--leaf)">Harrow Vale</text>
    </g>
  </svg>

</main>
</body>
</html>
```